Software Product Flyer Design

A established czech software company needs a marketing flyer to promote their software product and its modules.
The overall feel of the flyer must to be serious, but also eye-catching, enticing, clever and bold to attract customers.
Unifying graphic element is the new product logo.
The flyer would be A4, colour both sides and folded once (to give 4 pages of A5).
Title page - product logo with module name and module icon, short presentation of the product and list of its key features.
Inside pages - detailed informations with screenshots or graphical schemas.
Back side - informations about technical requirements and user support, contacts (address, phone, fax, e-mail, web pages - no social networks).
Product logo, module icon and some images attached.
Updates
Hello,
Reason: For organizational reasons we extending the deadline by 10 days.
FYI: We have uploaded the new ZIP file with previous version of our flyer.
Attached PDF file with text for inner pages.
Target Market(s)
Existing or new customers like municipalities, public authorities and nonprofit organizations.
Industry/Entity Type
Marketing
Requirements
Must have
- Winning designer must provide a template for Adobe InDesign based on his graphic design.
Avoid to using exotic fonts - in Czech we use Latin Extended characters (like áéěíýůčřžšťďň).
Nice to have
- Using graphic motif from product logo like as attached splash screen.

```html
<!DOCTYPE html>
<html lang="en">
<head>
<meta charset="utf-8">
<title>Ardent – Software Product Flyer</title>
<link rel="stylesheet" href="https://fonts.googleapis.com/css2?family=Didact+Gothic&family=PT+Sans:wght@400;700&display=swap">
<style>
  :root {
    --stage: #e9e7e4;
    --paper: #ffffff;
    --slate: #454a52;
    --orange: #f26522;
    --orange-light: #f7874a;
    --ink: #222222;
    --white: #ffffff;
    --sky-light: #eef5fb;
    --sky: #7fc4ea;
    --sky-deep: #1b6fb8;
  }
  * { box-sizing: border-box; margin: 0; padding: 0; }
  html, body { width: 1200px; height: 889px; overflow: hidden; background: var(--stage); }
  .canvas { position: relative; width: 1200px; height: 889px; overflow: hidden; }
  .flyer {
    position: absolute; left: 20px; top: 35px;
    width: 1232px; height: 870px;
    transform: scale(0.9416); transform-origin: 0 0;
    box-shadow: 0 4px 18px rgba(0,0,0,.18);
  }
  .page { position: absolute; top: 0; height: 870px; width: 616px; }
  .page--back { left: 0; background: var(--paper); }
  .page--front { left: 616px; background: var(--slate); }

  .pill {
    position: absolute; height: 48px; border-radius: 24px;
    background: linear-gradient(var(--orange-light), var(--orange) 55%);
    color: var(--white); display: flex; align-items: center;
    box-shadow: 0 10px 8px -6px rgba(0,0,0,.35);
  }
  .pill--support {
    left: 102px; top: 130px; width: 312px; padding-left: 38px;
    font-family: "PT Sans", sans-serif; font-size: 34px; z-index: 2;
  }
  .info-panel {
    position: absolute; left: 18px; top: 182px; width: 598px; height: 543px;
    background: var(--slate); border-radius: 30px 0 0 30px;
  }
  .info-panel__text {
    position: absolute; left: 44px; top: 131px; width: 510px;
    font-family: "Didact Gothic", sans-serif; font-size: 17px; line-height: 32px;
    color: var(--white);
  }
  .contacts {
    position: absolute; left: 52px; top: 490px; display: flex; gap: 22px;
    font-family: "PT Sans", sans-serif; font-size: 15px; color: var(--white);
    align-items: center;
  }
  .contact { display: flex; align-items: center; gap: 10px; }
  .contact__badge {
    width: 25px; height: 25px; border-radius: 50%; background: var(--orange);
    display: flex; align-items: center; justify-content: center; font-size: 14px;
  }
  .address {
    position: absolute; left: 0; width: 616px; top: 795px; text-align: center;
    font-family: "PT Sans", sans-serif; font-size: 16px; color: var(--ink);
  }

  .brand {
    position: absolute; left: 0; width: 616px; top: 88px;
    display: flex; justify-content: center; align-items: center; gap: 14px;
    font-family: "Didact Gothic", sans-serif; font-size: 62px; line-height: 1; color: var(--white);
  }
  .brand__mark { width: 34px; height: 34px; background: var(--orange); border-radius: 6px; }
  .visual {
    position: absolute; left: 6px; top: 182px; width: 589px; height: 543px;
    border-radius: 0 30px 30px 0; overflow: hidden;
    background:
      radial-gradient(circle at 58% 52%, var(--sky) 0, rgba(127,196,234,.35) 34%, transparent 55%),
      linear-gradient(180deg, var(--sky-light) 0 30%, var(--sky-deep) 31% 70%, var(--sky-light) 71%);
  }
  .pill--module {
    left: 153px; top: 675px; width: 310px; justify-content: center;
    font-family: "Didact Gothic", sans-serif; font-size: 32px; letter-spacing: 5px;
  }
  .website {
    position: absolute; left: 0; width: 616px; top: 788px; text-align: center;
    font-family: "Didact Gothic", sans-serif; font-size: 22px; letter-spacing: 5px; color: var(--white);
  }
</style>
</head>
<body>
<div class="canvas">
  <div class="flyer">
    <section class="page page--back">
      <div class="pill pill--support">USER SUPPORT</div>
      <div class="info-panel">
        <p class="info-panel__text">Lorem ipsum dolor sit amet, consectetuer adipiscing elit, sed diam nonummy nibh euismod tincidunt ut laoreet dolore magna aliquam erat volutpat. Ut wisi enim ad minim veniam, quis nostrud exerci tation ullamcorper suscipit lobortis nisl ut aliquip ex ea commodo consequat. Duis autem vel eum iriure dolor in hendrerit in vulputate velit esse molestie consequat, vel illum dolore eu feugiat nulla facilisis at vero eros et accumsan et iusto odio dignissim qui blandit praesent luptatum zzril delenit augue duis dolore te feugait nulla facilisi.</p>
        <div class="contacts">
          <span class="contact"><span class="contact__badge">P</span>012 - 456 - 7890</span>
          <span class="contact"><span class="contact__badge">F</span>012 - 456 - 7890</span>
          <span class="contact"><span class="contact__badge">E</span>info@ardent-soft.com</span>
        </div>
      </div>
      <p class="address">Suite 000 Cityname, Countryname 0000 00</p>
    </section>

    <section class="page page--front">
      <div class="brand"><span class="brand__mark"></span><span>Ardent</span></div>
      <div class="visual" role="img" aria-label="Module illustration: address book with letter A and a pencil over a blue circuit-board background"></div>
      <div class="pill pill--module">module name</div>
      <p class="website">www.ardent-soft.com</p>
    </section>
  </div>
</div>
</body>
</html>
```